Business Cards for new orthopaedic surgery practice

My husband and I are starting our own orthopaedic surgery practice. We are looking for a business card that is uniform, but one will have my name/title and the other will have his. You can just create one design with my name on it for now. But when I choose your design as the winning design I will ask that you add another copy with his name/title.

We are looking for classy, simple, elite all in one. We like dark blues/a little gold/yellow. Something that goes with our logo. We want our logo incorporated. Here is all the info you need:
Business name: RV Bone & Vitality Center
Location: 38517 North Willowmere Ave
Palm Crest, FL 33482
Phone: 954-218-4063
Fax: 954-582-7341
Email: info@myrvbonecare.example

Names: Lydia Vance, M.D.
Board Certified Hand and Upper Extremity Surgeon

Ebo Dansu, M.D.
Board Certified Hip & Knee Replacement/General Orthopaedic Surgeon

Can decide what you want to put on the back. Maybe a slogan:
Grounded in Skill. Centered on You

I am just going to upload our logo. The only thing is if we select you as the winning design, the location, and phone numbers may change. We will need your help to update that once fully solidified.

Industry/Entity Type

Medical

Contact Information for Business Card

Colors
0054AA
0677BA
7BADD7
CADEEF
E8F1F8
0094D4
00A9DD
6FCCEA
C7EBF8
E9F6FB

Requirements
Must have
• class, appeal,
Should not have
• We want to air on the side of masculine if we are looking at masculine vs. feminine feel. But we still want it classy, sophisticated, and something we will love

```html
<!DOCTYPE html>
<html lang="en">
<head>
<meta charset="utf-8">
<title>RV Bone &amp; Vitality Center — Business Card</title>
<link rel="stylesheet" href="https://fonts.googleapis.com/css2?family=Libre+Baskerville:wght@400;700&family=Figtree:wght@400;500&display=swap">
<style>
  :root {
    --backdrop: #1b1b1d;
    --card-white: #f4f4f3;
    --navy: #1c2a52;
    --navy-card: #1d2c56;
    --navy-emboss: #3a5288;
    --gold: #c59d58;
    --ink: #2c2c30;
  }
  * { margin: 0; padding: 0; box-sizing: border-box; }
  html, body {
    width: 1200px; height: 1059px; overflow: hidden;
    background: var(--backdrop);
  }
  .stage { position: relative; width: 1200px; height: 1059px; }

  .card {
    position: absolute;
    border-radius: 18px;
    overflow: hidden;
  }
  .card-front {
    left: 256px; top: 89px; width: 688px; height: 390px;
    background: var(--card-white);
  }
  .card-back {
    left: 254px; top: 547px; width: 693px; height: 393px;
    background: var(--navy-card);
  }

  /* Brand mark (front) */
  .brand {
    position: absolute; left: 37px; top: 64px;
    display: flex; align-items: center; gap: 10px;
  }
  .brand-dot {
    width: 16px; height: 16px; border-radius: 50%;
    background: var(--gold); flex: none;
  }
  .brand-name {
    font-family: "Libre Baskerville", serif;
    font-weight: 700; font-size: 17px; line-height: 1.3;
    color: var(--navy); letter-spacing: 0.02em;
  }

  .person-name {
    position: absolute; left: 37px; top: 156px;
    font-family: "Libre Baskerville", serif; font-weight: 700;
    font-size: 21px; color: var(--navy); letter-spacing: 0.01em;
  }
  .person-name .credential { color: var(--gold); }

  .details {
    position: absolute; left: 37px;
    font-family: "Figtree", sans-serif; font-size: 16.5px;
    line-height: 20.5px; color: var(--ink);
  }
  .title { top: 185px; }
  .address { top: 237px; }

  .contact-list {
    position: absolute; left: 37px; top: 287px; list-style: none;
    font-family: "Figtree", sans-serif; font-size: 16px; color: var(--ink);
  }
  .contact-list li {
    display: flex; align-items: center; gap: 7px; height: 24.5px;
  }
  .contact-list svg { width: 13px; height: 13px; fill: var(--gold); flex: none; }

  /* Back */
  .back-brand {
    position: absolute; left: 0; right: 0; top: 126px;
    display: flex; flex-direction: column; align-items: center; gap: 14px;
  }
  .back-ring {
    width: 22px; height: 22px; border-radius: 50%;
    border: 2px solid var(--navy-emboss);
  }
  .back-brand-name {
    font-family: "Libre Baskerville", serif; font-weight: 700;
    font-size: 26px; line-height: 1.35; text-align: center;
    color: var(--navy-emboss); letter-spacing: 0.04em;
  }
  .slogan {
    position: absolute; left: 0; right: 0; top: 333px;
    text-align: center;
    font-family: "Figtree", sans-serif; font-weight: 500;
    font-size: 20px; color: var(--gold);
  }
</style>
</head>
<body>
<main class="stage">
  <section class="card card-front">
    <div class="brand">
      <span class="brand-dot"></span>
      <span class="brand-name">RV Bone &amp;<br>Vitality Center</span>
    </div>

    <h1 class="person-name">LYDIA VANCE, <span class="credential">M.D.</span></h1>
    <p class="details title">Board Certified Hand and<br>Upper Extremity Surgeon</p>
    <p class="details address">38517 North Willowmere Ave<br>Palm Crest, FL 33482</p>

    <ul class="contact-list">
      <li>
        <svg viewBox="0 0 24 24" aria-hidden="true"><path d="M6.6 10.8a15.1 15.1 0 0 0 6.6 6.6l2.2-2.2a1 1 0 0 1 1-.25 11.4 11.4 0 0 0 3.6.57 1 1 0 0 1 1 1V20a1 1 0 0 1-1 1A17 17 0 0 1 3 4a1 1 0 0 1 1-1h3.5a1 1 0 0 1 1 1c0 1.25.2 2.45.57 3.57a1 1 0 0 1-.25 1z"/></svg>
        954-218-4063
      </li>
      <li>
        <svg viewBox="0 0 24 24" aria-hidden="true"><path d="M6 2h12v5H6zM4 8h16a2 2 0 0 1 2 2v7h-4v5H6v-5H2v-7a2 2 0 0 1 2-2zm4 8v4h8v-4z"/></svg>
        954-582-7341
      </li>
      <li>
        <svg viewBox="0 0 24 24" aria-hidden="true"><path d="M2 5h20v14H2zm2 2v.5l8 5 8-5V7zm0 2.8V17h16V9.8l-8 5z"/></svg>
        info@myrvbonecare.example
      </li>
    </ul>
  </section>

  <section class="card card-back">
    <div class="back-brand">
      <span class="back-ring"></span>
      <span class="back-brand-name">RV Bone &amp;<br>Vitality Center</span>
    </div>
    <p class="slogan">Grounded in Skill. Centered on You</p>
  </section>
</main>
</body>
</html>
```